The Korvane LLC Asset Classes

I'm looking for for two designs here to go into powerpoint and potentially as a standalone PDF. My company does wealth management.
Graphic Image #1
I break down the investment world into 4 broad categories
-Preservation
-Capital Markets
-Real Estate
-Alternatives
In each broad category, there are subcategories:
Preservation: cash, checking/savings accounts, money market accounts, CD's, and fixed annuities.
Capital Markets: Publicly traded stocks and bonds
Real Estate: single-family residence, retail, industrial, multifamily, and office
Alternatives: private equity, private credit, cryptocurrency, asset-backed loans, tax liens, oil & gas, litigation finance, and royalties
Graphic 2: Please see the bottom f page 1 of the Tessolin Decks PDF.
Just like in graphic one, you have 4 categories of the Capital Markets and their respective subcategories
Category 1: Domestic Stocks: Subcategories are Large, mid, and small size companies
Category 2: International Stocks: Subcategories are Large, Mid/Small and by region - Developed and Emerging
Category 3: Fixed Income: You have subcategories like corporate, municipal, government, domestic, international
Category 4: Alternatives: The subcategories are metals and real estate
---------------------
I'm looking to create a graphic (either pie chart, or a circle broken into parts or some other clever way to illustrate this) to clearly illustrate both of these universes in a clean, professional, slick manner.
Target Market(s)
Investors
Colors
Designer to choose colors to be used in the design.
Requirements
Must have
- Clean
- professional
- Easy to read
- Creative
- Visually appealling
Nice to have
- I have attached my logo and some marketing materials so you can get a feel of what I am doing. Maybe you can clean this up too!

```html
<!DOCTYPE html>
<html lang="en">
<head>
<meta charset="utf-8">
<title>Total Asset Allocation – Korvane LLC</title>
<link href="https://fonts.googleapis.com/css2?family=PT+Sans:wght@400;700&family=Nunito:wght@800;900&family=Hind:wght@400&display=swap" rel="stylesheet">
<style>
  :root{
    --orange:#f08a3c;
    --navy:#1d4f7a;
    --green:#5fb45e;
    --green-dark:#2e7d32;
    --blue:#0a6aad;
    --blue-dark:#0b4c7d;
    --brown:#a97c52;
    --brown-dark:#6e4c30;
    --grey:#a4a4a4;
    --grey-dark:#5e5e5e;
    --white:#ffffff;
  }
  *{margin:0;padding:0;box-sizing:border-box}
  html,body{width:1200px;height:1000px;overflow:hidden;background:#ffffff}
  .slide{position:absolute;left:0;top:50px;width:1200px;height:900px;background:var(--white)}
  .slide-title{position:absolute;left:49px;top:50px;font-family:"Hind",sans-serif;font-weight:400;
    font-size:47px;color:var(--orange);letter-spacing:0.5px;line-height:1}
  .brand{position:absolute;left:875px;top:60px;display:flex;align-items:center;gap:10px;
    font-family:"PT Sans",sans-serif;font-weight:700;font-size:30px;color:var(--navy)}
  .brand-dot{width:34px;height:34px;border-radius:50%;background:var(--navy)}
  .chain{position:absolute;left:0;top:0;width:1200px;height:900px}
  .chain-label{font-family:"Nunito",sans-serif;font-weight:900;font-size:16px;fill:var(--white);letter-spacing:0.8px}
  .category{position:absolute;top:353px;width:120px;height:484px;display:flex;flex-direction:column;
    align-items:center;justify-content:space-evenly;padding:10px 0 4px;
    box-shadow:-14px 18px 22px rgba(90,90,120,0.18);
    font-family:"PT Sans",sans-serif;font-size:15px;color:var(--white);text-align:center;line-height:1.28}
  .category::before{content:"";position:absolute;left:0;top:0;width:100%;height:7px;background:var(--strip)}
  .category::after{content:"";position:absolute;left:50%;top:-11px;margin-left:-11px;
    border-left:11px solid transparent;border-right:11px solid transparent;border-bottom:11px solid var(--strip)}
  .category .divider{width:70px;height:1px;background:rgba(255,255,255,0.9)}
  .category--preservation{left:247px;background:var(--green);--strip:var(--green-dark)}
  .category--capital{left:446px;background:var(--blue);--strip:var(--blue-dark)}
  .category--realestate{left:645px;background:var(--brown);--strip:var(--brown-dark)}
  .category--alternatives{left:845px;background:var(--grey);--strip:var(--grey-dark)}
</style>
</head>
<body>
<main class="slide">
  <h1 class="slide-title">Total Asset Allocation</h1>
  <div class="brand"><span class="brand-dot"></span><span>Korvane LLC</span></div>

  <svg class="chain" viewBox="0 0 1200 900" aria-hidden="true">
    <defs>
      <linearGradient id="link-green-blue" x1="0" x2="1"><stop offset="0.3" stop-color="#5fb45e"/><stop offset="0.75" stop-color="#0a6aad"/></linearGradient>
      <linearGradient id="link-blue-brown" x1="0" x2="1"><stop offset="0.3" stop-color="#0a6aad"/><stop offset="0.75" stop-color="#a97c52"/></linearGradient>
      <linearGradient id="link-brown-grey" x1="0" x2="1"><stop offset="0.3" stop-color="#a97c52"/><stop offset="0.75" stop-color="#a4a4a4"/></linearGradient>
      <filter id="soft" x="-30%" y="-30%" width="160%" height="160%"><feDropShadow dx="-6" dy="8" stdDeviation="8" flood-color="#555" flood-opacity="0.25"/></filter>
      <path id="arc-1" d="M249 238 A58 58 0 0 1 365 238"/>
      <path id="arc-2" d="M448 238 A58 58 0 0 1 564 238"/>
      <path id="arc-3" d="M647 238 A58 58 0 0 1 763 238"/>
      <path id="arc-4" d="M846 238 A58 58 0 0 1 962 238"/>
    </defs>

    <g class="links" filter="url(#soft)">
      <path fill="url(#link-green-blue)" d="M307 176 C357 176 366 206 406 206 C446 206 456 176 506 176 L506 300 C456 300 446 271 406 271 C366 271 357 300 307 300Z"/>
      <path fill="url(#link-blue-brown)" d="M506 176 C556 176 565 206 605 206 C645 206 655 176 705 176 L705 300 C655 300 645 271 605 271 C565 271 556 300 506 300Z"/>
      <path fill="url(#link-brown-grey)" d="M705 176 C755 176 764 206 804 206 C844 206 854 176 904 176 L904 300 C854 300 844 271 804 271 C764 271 755 300 705 300Z"/>
      <circle cx="307" cy="238" r="73" fill="var(--green)"/>
      <circle cx="506" cy="238" r="73" fill="var(--blue)"/>
      <circle cx="705" cy="238" r="73" fill="var(--brown)"/>
      <circle cx="904" cy="238" r="73" fill="var(--grey)"/>
    </g>

    <g class="hubs">
      <circle cx="307" cy="238" r="44" fill="#fff" filter="url(#soft)"/>
      <circle cx="506" cy="238" r="44" fill="#fff" filter="url(#soft)"/>
      <circle cx="705" cy="238" r="44" fill="#fff" filter="url(#soft)"/>
      <circle cx="904" cy="238" r="44" fill="#fff" filter="url(#soft)"/>
    </g>

    <g class="icon-preservation" fill="var(--green)">
      <circle cx="307" cy="230" r="13"/>
      <text x="307" y="236" text-anchor="middle" font-family="PT Sans, sans-serif" font-weight="700" font-size="17" fill="#fff">$</text>
      <rect x="299" y="207" width="2" height="7"/><rect x="306" y="204" width="2" height="9"/><rect x="313" y="207" width="2" height="7"/>
      <rect x="285" y="247" width="6" height="14"/>
      <path d="M292 249 L305 249 C310 249 310 254 305 254 L298 254 L310 254 L325 246 C329 245 330 249 327 251 L310 261 L292 259Z"/>
    </g>

    <g class="icon-capital" fill="var(--blue)">
      <rect x="481" y="238" width="7" height="22"/><rect x="491" y="230" width="7" height="30"/>
      <rect x="501" y="234" width="7" height="26"/><rect x="511" y="226" width="7" height="34"/><rect x="521" y="220" width="7" height="40"/>
      <path d="M480 232 L496 218 L507 226 L524 210" fill="none" stroke="var(--blue)" stroke-width="3.5"/>
      <path d="M517 208 L530 205 L527 218Z"/>
    </g>

    <g class="icon-realestate" fill="var(--brown)">
      <path d="M676 232 L705 213 L734 232 L730 235 L705 219 L680 235Z"/>
      <rect x="684" y="235" width="42" height="22"/>
      <rect x="699" y="245" width="12" height="12" fill="#fff"/>
      <rect x="702" y="248" width="6" height="9" fill="var(--brown)"/>
      <rect x="689" y="240" width="7" height="6" fill="#fff"/><rect x="714" y="240" width="7" height="6" fill="#fff"/>
    </g>

    <g class="icon-alternatives" stroke="var(--grey)" stroke-width="3" fill="var(--grey)">
      <line x1="904" y1="238" x2="904" y2="216"/><line x1="904" y1="238" x2="884" y2="228"/>
      <line x1="904" y1="238" x2="924" y2="240"/><line x1="904" y1="238" x2="892" y2="258"/>
      <line x1="904" y1="238" x2="910" y2="258"/><line x1="884" y1="228" x2="904" y2="216"/>
      <line x1="924" y1="240" x2="910" y2="258"/>
      <circle cx="904" cy="238" r="6"/><circle cx="904" cy="216" r="5"/><circle cx="884" cy="228" r="5"/>
      <circle cx="924" cy="240" r="6"/><circle cx="892" cy="258" r="5"/><circle cx="910" cy="258" r="4"/>
    </g>

    <text class="chain-label"><textPath href="#arc-1" startOffset="50%" text-anchor="middle">Preservation</textPath></text>
    <text class="chain-label"><textPath href="#arc-2" startOffset="50%" text-anchor="middle">Capital Markets</textPath></text>
    <text class="chain-label"><textPath href="#arc-3" startOffset="50%" text-anchor="middle">Real Estate</textPath></text>
    <text class="chain-label"><textPath href="#arc-4" startOffset="50%" text-anchor="middle">Alternatives</textPath></text>
  </svg>

  <section class="category category--preservation">
    <p>Cash</p><span class="divider"></span>
    <p>Checking/<br>Savings<br>Accounts</p><span class="divider"></span>
    <p>Money<br>Market<br>Funds</p><span class="divider"></span>
    <p>CD’s</p><span class="divider"></span>
    <p>Fixed<br>Annuities</p>
  </section>

  <section class="category category--capital">
    <p>Publicly-traded<br>stocks<br>and bonds</p>
  </section>

  <section class="category category--realestate">
    <p>Single-Family<br>Residences</p><span class="divider"></span>
    <p>Retail</p><span class="divider"></span>
    <p>Industrial</p><span class="divider"></span>
    <p>Multifamily</p><span class="divider"></span>
    <p>Office</p>
  </section>

  <section class="category category--alternatives">
    <p>Private Equity</p><span class="divider"></span>
    <p>Private Credit</p><span class="divider"></span>
    <p>Cryptocurrency</p><span class="divider"></span>
    <p>Asset-backed<br>Loans</p><span class="divider"></span>
    <p>Tax Liens</p><span class="divider"></span>
    <p>Oil &amp; Gas</p><span class="divider"></span>
    <p>Litigation<br>Finance</p><span class="divider"></span>
    <p>Royalties</p>
  </section>
</main>
</body>
</html>
```